KBT Business Cards

We require business cards for our business. We would like a matte black back to the card, with our logo centred in the middle. The front side of the card is open to design.

Target Market(s)

Clients looking for legal services (professional)

Industry/Entity Type

Legal

Contact Information for Business Card

Doran Kelbrath
Partner
Mobile: 0461 738 524
Email: doran@kbtlaw.co
Website: www.kbtlaw.co
Level 3, 118 Wendmore Street
Sydney NSW 2000

Font styles to use
Other font styles liked:
• Avenir

Colors
f04a50
ffffff
1b1b1b

Requirements
Must have
• Black back with logo included in the centre of the card.
• Our font is Avenir.

```html
<!DOCTYPE html>
<html lang="en">
<head>
<meta charset="utf-8">
<title>KBT Legal – Business Cards</title>
<link href="https://fonts.googleapis.com/css2?family=Nunito+Sans:wght@400;600;700&family=Oswald:wght@500&display=swap" rel="stylesheet">
<style>
  :root {
    --backdrop: #141414;
    --card: #1b1b1b;
    --card-edge: #232323;
    --accent: #f04a50;
    --white: #ffffff;
    --muted: #d9d9d9;
  }
  * { margin: 0; padding: 0; box-sizing: border-box; }
  html, body { width: 1200px; height: 900px; overflow: hidden; }
  body {
    background: radial-gradient(ellipse at 50% 40%, #262626 0%, var(--backdrop) 70%);
    font-family: "Nunito Sans", "Avenir", sans-serif;
    position: relative;
  }
  .card {
    position: absolute;
    left: 300px;
    width: 600px;
    height: 343px;
    background: var(--card);
    border: 1px solid var(--card-edge);
    box-shadow: 0 18px 40px rgba(0,0,0,0.6);
    overflow: hidden;
  }
  .card--back { top: 70px; }
  .card--front { top: 470px; }

  /* back */
  .back__pattern {
    position: absolute;
    left: 250px; top: 0;
    width: 350px; height: 100%;
    background: linear-gradient(100deg, rgba(27,27,27,0) 0%, rgba(80,80,80,0.35) 45%, rgba(110,110,110,0.45) 100%);
  }
  .brand {
    position: absolute;
    left: 110px; top: 150px;
    display: flex; align-items: center; gap: 12px;
  }
  .brand__square {
    width: 30px; height: 30px;
    background: var(--accent);
  }
  .brand__name {
    color: var(--white);
    font-weight: 700;
    font-size: 18px;
    letter-spacing: 1.5px;
    text-transform: uppercase;
  }

  /* front */
  .identity {
    position: absolute;
    right: 310px; top: 118px;
    text-align: right;
  }
  .identity__name {
    font-family: "Oswald", "Avenir", sans-serif;
    font-weight: 500;
    font-size: 34px;
    line-height: 1;
    color: var(--accent);
    text-transform: uppercase;
    letter-spacing: 0.3px;
  }
  .identity__title {
    margin-top: 10px;
    font-size: 17px;
    color: var(--white);
    letter-spacing: 0.5px;
  }
  .divider {
    position: absolute;
    left: 305px; top: 118px;
    width: 1.5px; height: 74px;
    background: var(--accent);
  }
  .contacts {
    position: absolute;
    left: 325px; top: 120px;
    list-style: none;
  }
  .contacts__item {
    display: flex; align-items: center; gap: 9px;
    font-size: 16px;
    color: var(--white);
    letter-spacing: 0.4px;
    line-height: 24px;
  }
  .contacts__icon { width: 11px; height: 11px; flex: none; }
  .address {
    position: absolute;
    left: 0; right: 0; bottom: 42px;
    text-align: center;
    font-size: 16px;
    color: var(--white);
    letter-spacing: 0.4px;
  }
</style>
</head>
<body>

<section class="card card--back" aria-label="Card back">
  <div class="back__pattern" role="img" aria-label="Embossed repeating pattern of the brand symbol in soft grey tones"></div>
  <div class="brand">
    <span class="brand__square"></span>
    <span class="brand__name">KBT Legal</span>
  </div>
</section>

<section class="card card--front" aria-label="Card front">
  <div class="identity">
    <h1 class="identity__name">Doran Kelbrath</h1>
    <p class="identity__title">General Manager</p>
  </div>
  <div class="divider"></div>
  <ul class="contacts">
    <li class="contacts__item">
      <svg class="contacts__icon" viewBox="0 0 12 12"><path d="M2.5 1 L4.5 1 L5 3.5 L3.8 4.5 Q5 7 7.5 8.2 L8.5 7 L11 7.5 L11 9.5 Q10.5 11 9 11 Q1 10 1 3 Q1 1.5 2.5 1Z" fill="var(--accent)"/></svg>
      0461 738 524
    </li>
    <li class="contacts__item">
      <svg class="contacts__icon" viewBox="0 0 12 12"><rect x="0.75" y="2.25" width="10.5" height="7.5" fill="none" stroke="var(--accent)" stroke-width="1.2"/><path d="M1 2.6 L6 6.6 L11 2.6" fill="none" stroke="var(--accent)" stroke-width="1.2"/></svg>
      doran@kbtlaw.co
    </li>
    <li class="contacts__item">
      <svg class="contacts__icon" viewBox="0 0 12 12"><g fill="none" stroke="var(--accent)" stroke-width="1"><circle cx="6" cy="6" r="5"/><ellipse cx="6" cy="6" rx="2.2" ry="5"/><path d="M1 6 H11 M2 3.3 H10 M2 8.7 H10"/></g></svg>
      www.kbtlaw.co
    </li>
  </ul>
  <p class="address">Level 3, 118 Wendmore Street Sydney NSW 2000</p>
</section>

</body>
</html>
```